New Design for Brindlecovex [Weebly]

Hello, This is my 2nd project here. I need a new web design for www.brindlecovex.com.au which is one of my clients, and an extremely outdated website. It only has a few links and is fairly straight forward, looking for a more professional, up-to-date looking website. Please note: The website will be made under a weekly white-label platform, so the design MUST be consistent with this type of platform. Many more projects will be up and coming so the best designers will definitely be selected for future projects.
Thankyou

Industry/Entity Type

It Professional

Requirements
Must have
• Please refer to www.brindlecovex.com.au to find all the content.

```html
<!DOCTYPE html>
<html lang="en">
<head>
<meta charset="utf-8">
<title>Brindlecovex – Thermal and Sealing Specialists</title>
<link href="https://fonts.googleapis.com/css2?family=Arimo:wght@400;700&display=swap" rel="stylesheet">
<style>
:root{
  --page:#e4e4e4;
  --panel:#ffffff;
  --ink:#333333;
  --muted:#7a7a7a;
  --accent:#e05a1c;
  --green:#6cb33f;
  --link:#2b8fd6;
  --dark:#262626;
  --nav-active:#2d2d2d;
  --rule:#e2e2e2;
}
*{margin:0;padding:0;box-sizing:border-box}
html,body{width:769px;height:1200px;overflow:hidden}
body{background:var(--page);font-family:"Arimo",Arial,sans-serif;color:var(--ink);position:relative}

.site-header{position:absolute;left:0;top:0;width:769px;height:96px}
.brand{position:absolute;left:96px;top:30px;display:flex;align-items:flex-start;gap:8px}
.brand-mark{width:30px;height:30px;background:var(--accent);margin-top:2px}
.brand-name{font-size:22px;font-weight:700;color:var(--accent);line-height:24px}
.brand-tag{font-size:11px;color:var(--muted);margin-top:3px}

.main-nav{position:absolute;left:356px;top:62px;display:flex}
.main-nav a{display:block;font-size:9px;font-weight:700;color:var(--ink);text-decoration:none;padding:6px 9px;text-transform:uppercase;letter-spacing:.3px}
.main-nav a.active{background:var(--nav-active);color:#fff;border-radius:2px}

.content-panel{position:absolute;left:82px;top:98px;width:606px;height:982px;background:var(--panel);border-radius:6px;box-shadow:0 1px 6px rgba(0,0,0,.18)}

.hero{position:absolute;left:20px;top:18px;width:566px;height:228px;background:linear-gradient(135deg,#6b4a3a,#c9a07a 35%,#7a8c9a 60%,#4a3a32);border-radius:2px}

.intro{position:absolute;left:22px;top:262px;width:562px;font-size:8.5px;line-height:13px;color:var(--muted)}

.section-title{position:absolute;left:22px;display:flex;align-items:center;gap:8px;font-size:10.5px;font-weight:700;color:var(--ink)}
.section-title::before{content:"";width:12px;height:12px;border-radius:50%;background:#fff;border:3px solid #bdbdbd}

.bullet-cols{position:absolute;left:42px;width:540px;display:grid;grid-template-columns:repeat(3,1fr);column-gap:14px}
.bullet-cols ul{list-style:none}
.bullet-cols li{position:relative;padding-left:11px;font-size:8px;line-height:13px;color:var(--muted)}
.bullet-cols li::before{content:"";position:absolute;left:0;top:4px;width:5px;height:5px;border-radius:50%;background:var(--green)}

.carousel{position:absolute;left:22px;top:626px;width:562px;height:188px;border-top:1px solid var(--rule);border-bottom:1px solid var(--rule)}
.carousel-arrow{position:absolute;top:64px;width:14px;height:22px}
.carousel-arrow.prev{left:2px}
.carousel-arrow.next{right:2px}
.carousel-track{position:absolute;left:24px;top:14px;width:514px;display:grid;grid-template-columns:repeat(4,1fr);column-gap:10px}
.product-card{text-align:center}
.product-photo{height:118px;border:1px solid #d0d0d0}
.product-photo.p1{background:linear-gradient(160deg,#b7b7b7,#8a8a8a)}
.product-photo.p2{background:linear-gradient(160deg,#d8c6b3,#9c7f67)}
.product-photo.p3{background:linear-gradient(160deg,#c9c2b5,#7f7a70)}
.product-photo.p4{background:linear-gradient(160deg,#8aa0b4,#4d5f70)}
.product-caption{font-size:8px;line-height:11px;color:var(--ink);margin-top:6px}

.category{position:absolute;left:22px;top:866px;width:562px;display:grid;grid-template-columns:128px repeat(3,1fr)}
.category .section-title{position:static}
.category ul{list-style:none}
.category li{font-size:8px;line-height:19px;color:var(--link)}

.site-footer{position:absolute;left:0;top:1104px;width:769px;height:96px;background:var(--dark);color:#9a9a9a;font-size:8px;line-height:11px}
.footer-address{position:absolute;left:96px;top:14px}
.footer-address strong{color:#d0d0d0}
.footer-copy{position:absolute;right:82px;top:62px}
</style>
</head>
<body>

<header class="site-header">
  <div class="brand">
    <span class="brand-mark"></span>
    <div>
      <div class="brand-name">Brindlecovex</div>
      <div class="brand-tag">Thermal and Sealing Specialists</div>
    </div>
  </div>
  <nav class="main-nav">
    <a class="active" href="#">Home</a>
    <a href="#">About Us</a>
    <a href="#">Product</a>
    <a href="#">Service</a>
    <a href="#">Our Client</a>
    <a href="#">Contact</a>
  </nav>
</header>

<main class="content-panel">
  <div class="hero" role="img" aria-label="Collage of thermal fabric, seals and insulation product photos"></div>

  <p class="intro">Brindlecovex are one of Australia's leading suppliers and manufacturers of thermal fabrics and fabrications. The experience, knowledge and facility to design and fabricate gives you the quality Australian made products you demand.</p>

  <h2 class="section-title" style="top:318px">Thermal and Sealing Specialists</h2>
  <div class="bullet-cols" style="top:344px">
    <ul>
      <li>Thermal Fabrics and Fabrications</li>
      <li>High and Low Temperature Insulation</li>
      <li>Furnace / Oven Door Seals</li>
      <li>Welding Blankets and Curtains</li>
      <li>Fabric Expansion Joints</li>
    </ul>
    <ul>
      <li>Boiler Exhaust Covers</li>
      <li>Thermal Hoses / Covers</li>
      <li>Acoustic Materials</li>
      <li>Pump and Valve Packings</li>
      <li>Custom Materials</li>
    </ul>
    <ul>
      <li>Standard and Non-Standard Gaskets</li>
      <li>Boilers Gaskets and Seals</li>
      <li>Gland Packing</li>
      <li>Fabric Seal</li>
      <li>and Lots more</li>
    </ul>
  </div>

  <h2 class="section-title" style="top:440px">Thermal Product available at Brindlecovex</h2>
  <div class="bullet-cols" style="top:466px">
    <ul>
      <li>Ceramic Fibre Tapes, Ropes, Sleeves, Boards &amp; Insulation</li>
      <li>High Temp Glass Fibre Tapes, Ropes, Sleeves, Boards &amp; Insulation</li>
      <li>Furnace / Oven Tadpole Tape Seals</li>
      <li>Boiler Tapes, Seals &amp; Gaskets</li>
    </ul>
    <ul>
      <li>Boiler Close Up Ink</li>
      <li>Welding Blankets, Curtains &amp; Screens</li>
      <li>Exhaust Thermal / Acoustic Covers</li>
      <li>Thermal Hoses / Covers</li>
    </ul>
    <ul>
      <li>Machine Thermal Covers</li>
      <li>Thermal Fabrics</li>
      <li>Thermal Fabrications to Your Specification</li>
      <li>Fabric / Metallic Expansion Joints &amp; Associated Metal Work</li>
    </ul>
  </div>

  <h2 class="section-title" style="top:594px">Product Overview</h2>
  <div class="carousel">
    <svg class="carousel-arrow prev" viewBox="0 0 14 22"><path d="M10 4 L4 11 L10 18" fill="none" stroke="#555" stroke-width="2.5"/></svg>
    <div class="carousel-track">
      <div class="product-card">
        <div class="product-photo p1" role="img" aria-label="Thermal product photo"></div>
        <div class="product-caption">Thermal</div>
      </div>
      <div class="product-card">
        <div class="product-photo p2" role="img" aria-label="Fabric expansion joint photo"></div>
        <div class="product-caption">Fabric Expansion Joint<br>Type C/F</div>
      </div>
      <div class="product-card">
        <div class="product-photo p3" role="img" aria-label="Boiler close up ink tins photo"></div>
        <div class="product-caption">Boiler Close Up Ink</div>
      </div>
      <div class="product-card">
        <div class="product-photo p4" role="img" aria-label="Fabric expansion joint photo"></div>
        <div class="product-caption">Fabric Expansion Joint<br>Type M</div>
      </div>
    </div>
    <svg class="carousel-arrow next" viewBox="0 0 14 22"><path d="M4 4 L10 11 L4 18" fill="none" stroke="#555" stroke-width="2.5"/></svg>
  </div>

  <div class="category">
    <h2 class="section-title">Category Product</h2>
    <ul>
      <li>Printed Tape</li>
      <li>Tadpole Tape</li>
      <li>Glass Fabric Roads</li>
      <li>Glass Fabric</li>
    </ul>
    <ul>
      <li>Gland Packing</li>
      <li>Welding Blankets</li>
      <li>Expansion Joints</li>
      <li>Boiler Covers</li>
    </ul>
    <ul>
      <li>Injection Machine</li>
      <li>Acoustic Cover</li>
      <li>Metal Exhaust Covers</li>
      <li>Valve Covers</li>
    </ul>
  </div>
</main>

<footer class="site-footer">
  <div class="footer-address">
    <strong>Brindlecovex Pty Ltd</strong><br>
    24 Harlow Way<br>
    Kestrel Park VIC 3175 Victoria Australia<br>
    Phone: 03 9000 2140<br>
    Fax: 03 9000 2141<br>
    Email: sales@brindlecovex.com.au<br>
    Contact: Office Team - Sales Desk
  </div>
  <div class="footer-copy">Copyright 2012 Brindlecovex Pty Ltd - All rights reserved</div>
</footer>

</body>
</html>
```